Bramwell IT Services Business Card

Bramwell IT Services are a Perth based IT Services company. We would like to incorporate our company logo (attached) and stick with the blue that is in that design. I would like a clean look design that isn't too busy, yet creates a lasting image that is instantly recognisable in the recipients mind.

Target Market(s)

The target audience is small/medium business owners.

Industry/Entity Type

Business

Font styles to use
Serif
Sans Serif

Colors

Designer to choose colors to be used in the design.

Requirements
Must have
• The design should include:
Business name: Bramwell IT Services
Directors Name: Marcus Tenley
Phone Number: 0483 562 904
Email: support@bramwellit.com.au
Website: www.bramwellit.com.au

```html
<!DOCTYPE html>
<html lang="en">
<head>
<meta charset="utf-8">
<title>Bramwell IT Services – Business Card</title>
<link rel="stylesheet" href="https://fonts.googleapis.com/css2?family=Arimo:wght@400;700&display=swap">
<style>
  :root {
    --brand-blue: #1f5cb5;
    --brand-blue-deep: #17489a;
    --band-dark: #2a2a2a;
    --band-grey: #a8a8a8;
    --card-white: #ffffff;
    --ink: #222222;
    --backdrop: #e9ebee;
  }
  * { margin: 0; padding: 0; box-sizing: border-box; }
  html, body {
    width: 1200px; height: 919px; overflow: hidden;
    background: var(--backdrop);
    font-family: "Arimo", Arial, sans-serif;
  }
  .canvas { position: relative; width: 1200px; height: 919px; }
  .card {
    position: absolute; width: 620px; height: 354px;
    background: var(--card-white); border-radius: 22px; overflow: hidden;
    box-shadow: 0 10px 28px rgba(0,0,0,.18);
  }
  .card-front { left: 90px; top: 80px; }
  .card-back { left: 490px; top: 480px; }
  .card-art { position: absolute; inset: 0; width: 100%; height: 100%; }

  .contact-list {
    position: absolute; right: 46px; top: 44px; list-style: none;
    text-align: right; font-size: 14.5px; line-height: 22px; color: var(--ink);
  }
  .contact-list li { display: flex; justify-content: flex-end; align-items: center; gap: 8px; }
  .contact-list svg { width: 13px; height: 13px; fill: var(--brand-blue); }

  .brand-mark { position: absolute; display: flex; align-items: center; gap: 10px; color: var(--brand-blue); font-weight: 700; }
  .brand-dot { border-radius: 50%; background: var(--brand-blue); flex: none; }
  .brand-name { display: flex; flex-direction: column; line-height: 1; }
  .brand-name .sub { letter-spacing: .35em; }

  .card-front .brand-mark { left: 40px; top: 150px; }
  .card-front .brand-dot { width: 40px; height: 40px; }
  .card-front .brand-name .main { font-size: 27px; }
  .card-front .brand-name .sub { font-size: 9px; margin-top: 4px; }

  .holder { position: absolute; left: 96px; top: 226px; }
  .holder-name { font-size: 20px; font-weight: 700; color: var(--brand-blue); }
  .holder-role { font-size: 14px; color: var(--ink); margin-top: 3px; }

  .card-back .brand-mark { left: 50%; top: 50%; transform: translate(-50%, -50%); gap: 14px; }
  .card-back .brand-dot { width: 62px; height: 62px; }
  .card-back .brand-name .main { font-size: 42px; }
  .card-back .brand-name .sub { font-size: 12px; margin-top: 6px; }
</style>
</head>
<body>
<main class="canvas">

  <section class="card card-front" aria-label="Business card front">
    <svg class="card-art" viewBox="0 0 620 354" preserveAspectRatio="none" aria-hidden="true">
      <path d="M0,0 H300 C200,30 100,55 0,76 Z" fill="var(--brand-blue)"/>
      <path d="M0,82 C180,70 300,100 400,150 C480,185 560,200 620,205 V225 C560,221 470,207 390,172 C290,124 170,98 0,104 Z" fill="var(--band-dark)"/>
      <path d="M620,238 C520,280 330,316 120,334 C80,338 40,340 0,342 V354 H620 Z" fill="var(--band-grey)"/>
      <path d="M620,246 C520,288 330,322 120,340 C80,344 40,346 0,348 V354 H620 Z" fill="var(--brand-blue)"/>
    </svg>
    <ul class="contact-list">
      <li>0483 562 904 <svg viewBox="0 0 16 16"><path d="M3 1h3l1.5 4-2 1.2a9 9 0 0 0 4.3 4.3L11 8.5l4 1.5v3a2 2 0 0 1-2 2A12 12 0 0 1 1 3a2 2 0 0 1 2-2z"/></svg></li>
      <li>support@bramwellit.com.au <svg viewBox="0 0 16 16"><path d="M1 3h14v10H1z M2 4l6 5 6-5" stroke="#fff" stroke-width="1"/></svg></li>
      <li>www.bramwellit.com.au <svg viewBox="0 0 16 16"><circle cx="8" cy="8" r="7"/><path d="M1 8h14M8 1c-3 4-3 10 0 14M8 1c3 4 3 10 0 14" stroke="#fff" stroke-width="1" fill="none"/></svg></li>
    </ul>
    <div class="brand-mark">
      <span class="brand-dot"></span>
      <span class="brand-name"><span class="main">BRAMWELL</span><span class="sub">IT SERVICES</span></span>
    </div>
    <div class="holder">
      <p class="holder-name">Marcus Tenley</p>
      <p class="holder-role">Director</p>
    </div>
  </section>

  <section class="card card-back" aria-label="Business card back">
    <svg class="card-art" viewBox="0 0 620 354" preserveAspectRatio="none" aria-hidden="true">
      <path d="M0,118 C40,88 120,60 200,56 C380,50 520,90 620,110 V0 H0 Z" fill="var(--brand-blue)"/>
      <path d="M620,250 C520,270 400,290 250,320 C190,332 140,344 110,354 H620 Z" fill="var(--brand-blue-deep)"/>
    </svg>
    <div class="brand-mark">
      <span class="brand-dot"></span>
      <span class="brand-name"><span class="main">BRAMWELL</span><span class="sub">IT SERVICES</span></span>
    </div>
  </section>

</main>
</body>
</html>
```